Wordpress template for a mens-choire webpage

Task is to design a Wordpress template for an 98 years old estonian mens choire webpage.
Design should involve details from the attached files, choire logo and the colors of the choire flag: in horizontal orientation bright sky-blue, white, bright grass-green.
Designer signature is allowed to be added to the template, with country of origin.

Reason: Deadline extended 2 days (until 2. March 2014) to accommodate designers creativity.

Thank you everyone for your great designs!
Our project has now entered into a voting and decision phase until 14th of March 2014 (included).

```html
<!DOCTYPE html>
<html lang="en">
<head>
<meta charset="utf-8">
<title>Kaskemäe Meeskoor</title>
<link href="https://fonts.googleapis.com/css2?family=Open+Sans:ital,wght@0,300;0,400;0,600;1,400&display=swap" rel="stylesheet">
<style>
:root{
  --red:#a3161a;
  --red-text:#a31a1e;
  --dark:#1e1e1e;
  --footer:#262626;
  --ink:#2a2a2a;
  --muted:#555;
  --panel:#f7f6f6;
  --news-bg:#efeeee;
  --gray-panel:#e2e2e2;
  --green:#6aa51a;
  --blue:#1b64b2;
}
*{margin:0;padding:0;box-sizing:border-box}
html,body{width:866px;height:1200px;overflow:hidden}
body{font-family:"Open Sans",Arial,sans-serif;color:var(--ink);background:#fff;position:relative}
.abs{position:absolute}

/* header */
.site-header{position:absolute;left:0;top:0;width:866px;height:90px;background:#fff}
.brand{position:absolute;left:76px;top:14px;display:flex;align-items:center;gap:8px}
.brand-mark{width:26px;height:26px;border-radius:50%;background:var(--red)}
.brand-name{font-size:14px;font-weight:600;color:var(--red-text)}
.contact-top{position:absolute;top:18px;left:578px;display:flex;align-items:center;gap:6px;font-size:12px;color:var(--red-text)}
.login{position:absolute;top:18px;left:705px;display:flex;align-items:center;gap:6px;font-size:11px;color:var(--red-text)}

/* nav */
.main-nav{position:absolute;left:0;top:90px;width:866px;height:38px;background:var(--dark)}
.main-nav a{position:absolute;top:0;height:38px;line-height:38px;font-size:11px;color:#fff;text-decoration:none}
.main-nav .active{left:71px;width:65px;background:var(--red);text-align:center}
.search{position:absolute;left:607px;top:7px;width:187px;height:24px;background:#fff;border-radius:2px;display:flex}
.search-btn{width:25px;height:24px;background:var(--red);display:flex;align-items:center;justify-content:center}
.search span{font-size:10px;font-style:italic;color:#888;line-height:24px;padding-left:7px}

/* hero */
.hero-photo{position:absolute;left:0;top:128px;width:658px;height:325px;background:linear-gradient(180deg,#2c2a2a 0%,#3b3030 45%,#5a3a2a 78%,#8a5a35 100%)}
.hero-arrow{position:absolute;top:269px;width:26px;height:26px;border-radius:50%;border:1px solid #bbb;background:rgba(0,0,0,.35)}
.cd-panel{position:absolute;left:658px;top:128px;width:208px;height:325px;background:var(--gray-panel)}
.cd-title{position:absolute;left:20px;top:42px;font-size:18px;color:var(--red-text);line-height:1}
.cd-sub{position:absolute;left:20px;top:62px;font-size:9.5px;font-weight:600;color:#222}
.cd-rule{position:absolute;left:20px;top:79px;width:163px;height:1px;background:#b8b8b8}
.cd-image{position:absolute;left:48px;top:100px;width:100px;height:92px;background:linear-gradient(135deg,#dfe0e2,#b3b5b8 60%,#b33b3b);transform:rotate(10deg)}
.cd-order{position:absolute;left:34px;top:226px;font-size:13px;font-weight:600;color:var(--red-text);line-height:1}
.cd-click{position:absolute;left:34px;top:241px;font-size:9.5px;color:#222}

/* content */
.content{position:absolute;left:71px;top:453px;width:725px;height:619px;background:var(--panel)}
h2{font-weight:400;font-size:18px;color:#222;position:absolute}
.copy{position:absolute;font-size:10.2px;line-height:12.2px;color:#333;text-align:justify;font-weight:400}
.video{position:absolute;left:424px;top:28px;width:275px;height:193px;background:radial-gradient(circle at 50% 45%,#d9c49b,#c9b07f 70%,#b89b68)}
.video-play{position:absolute;left:114px;top:67px;width:48px;height:34px;border-radius:8px;background:rgba(20,20,20,.8)}
.video-bar{position:absolute;left:0;bottom:0;width:275px;height:20px;background:#1b1b1b;font-size:7px;color:#ddd;line-height:20px;padding-left:56px}
.video-track{position:absolute;left:0;bottom:20px;width:275px;height:3px;background:#555}
.photo{position:absolute;width:152px;height:104px}
.view-all{position:absolute;left:287px;top:576px;font-size:10px;color:#333}
.news{position:absolute;left:426px;top:277px;width:273px;height:306px;background:var(--news-bg)}
.news-item{position:absolute;left:9px;width:260px}
.news-thumb{position:absolute;left:0;top:0;width:72px;height:66px}
.news-name{position:absolute;left:84px;top:-1px;font-size:12px;color:#333}
.news-handle{position:absolute;left:84px;top:15px;font-size:9.5px;color:#444}
.news-date{position:absolute;left:84px;top:38px;font-size:10px;font-weight:600;color:#333}
.news-text{position:absolute;left:84px;top:51px;width:175px;font-size:9.5px;line-height:11.5px;color:#444}
.news-rule{position:absolute;left:11px;width:240px;height:1px;background:#cfcfcf}

/* footer */
.site-footer{position:absolute;left:0;top:1072px;width:866px;height:128px;background:var(--footer);border-top:3px solid var(--red)}
.f-col{position:absolute;top:20px;font-size:10.5px;line-height:17.5px;color:#c9c9c9}
.f-col h4{font-weight:400;font-size:12px;color:#5a1212;line-height:18px}
.f-divider{position:absolute;top:3px;width:1px;height:125px;background:#3c3c3c}
.f-call{position:absolute;left:334px;top:24px;font-size:10.5px;color:#c9c9c9;line-height:13px}
.f-call b{display:block;font-weight:400;font-size:12px;color:#5a1212}
.f-mail{position:absolute;left:462px;top:30px;font-size:10.5px;color:#c9c9c9}
.social{position:absolute;top:21px;width:24px;height:24px;border-radius:4px}
.f-line{position:absolute;left:313px;top:85px;width:553px;height:1px;background:#3c3c3c}
.copyright{position:absolute;right:71px;top:105px;font-size:8px;color:#555}
</style>
</head>
<body>

<!-- flag backdrop -->
<svg class="abs" style="left:0;top:453px" width="866" height="619" viewBox="0 0 866 619" aria-hidden="true">
  <rect width="866" height="619" fill="#f1f1f1"/>
  <path d="M0 0H71V135C50 140 25 148 0 158Z" fill="var(--green)"/>
  <path d="M0 460C25 447 50 440 71 436V619H0Z" fill="var(--blue)"/>
  <path d="M796 0H866V150C845 135 820 125 796 120Z" fill="var(--green)"/>
  <path d="M796 415C820 405 845 405 866 410V619H796Z" fill="var(--blue)"/>
</svg>

<header class="site-header">
  <div class="brand"><span class="brand-mark"></span><span class="brand-name">Kaskemäe Meeskoor</span></div>
  <div class="contact-top">
    <svg width="20" height="20" viewBox="0 0 20 20"><circle cx="10" cy="10" r="9" fill="none" stroke="#333" stroke-width="1.4"/><path d="M7 5.5l1.6 2.4-1 1.2c.7 1.4 1.8 2.5 3.2 3.2l1.2-1 2.4 1.6-1 1.8c-3.6-.4-6.6-3.4-7-7z" fill="#333"/></svg>
    01632 960 418
  </div>
  <div class="login">
    <svg width="14" height="15" viewBox="0 0 14 15"><circle cx="7" cy="4" r="3.5" fill="#333"/><path d="M0 15c0-4 3-6 7-6s7 2 7 6z" fill="#333"/></svg>
    Member Login
  </div>
</header>

<nav class="main-nav">
  <a class="active" href="#">HOME</a>
  <a style="left:148px" href="#">ABOUT</a>
  <a style="left:214px" href="#">BROWSE</a>
  <a style="left:283px" href="#">HARBOUR PHOTO NEWS</a>
  <a style="left:433px" href="#">A-Z PEOPLE</a>
  <div class="search">
    <div class="search-btn"><svg width="12" height="12" viewBox="0 0 12 12"><circle cx="5" cy="5" r="3.6" fill="none" stroke="#fff" stroke-width="1.8"/><path d="M7.7 7.7l3.3 3.3" stroke="#fff" stroke-width="2"/></svg></div>
    <span>Search Choir CD's</span>
  </div>
</nav>

<section>
  <div class="hero-photo" role="img" aria-label="Men's choir in striped blazers performing on stage before an audience"></div>
  <div class="hero-arrow" style="left:26px"></div>
  <div class="hero-arrow" style="left:609px"></div>
  <aside class="cd-panel">
    <div class="cd-title">MEN'S CHOIR CDS</div>
    <div class="cd-sub">ORDER ONLINE!</div>
    <div class="cd-rule"></div>
    <div class="cd-image" role="img" aria-label="Choir CD cover showing singers in red jackets"></div>
    <div class="cd-order">ORDER ONLINE</div>
    <div class="cd-click">CLICK HERE TO PURCHASE</div>
    <svg class="abs" style="left:108px;top:264px" width="100" height="61" viewBox="0 0 100 61"><path d="M100 0V61H0L36 25Z" fill="#cfcfcf"/><path d="M100 0V61H38Z" fill="var(--red)"/><path d="M100 0V61H80Z" fill="var(--green)"/></svg>
  </aside>
</section>

<main class="content">
  <h2 style="left:33px;top:28px">WELCOME TO OUR WEBSITE!</h2>
  <p class="copy" style="left:33px;top:64px;width:362px">"The Northfield College Men's Choir is an auditioned group of male musicians. The choir has a strong heritage, dating to Fall 1895, and has served as an integral part of the college's music program. The NCMC performs a wide variety of both sacred and secular music and consists of not only Music majors but also Arts and Sciences, Business, Engineering, and Pre-Med students.</p>
  <p class="copy" style="left:33px;top:137px;width:362px">Past concert highlights include performances at Harbourside Hall, Saint Anselm Chapel in New York, and the Lakeland Music Educators Convention. Recently, the NCMC opened for the Western Choral Directors Association Convention in Maple Falls. The choir has also toured internationally including a recent trip to Africa and Argentina.</p>

  <div class="video" role="img" aria-label="Video player with archival choir emblem artwork">
    <div class="video-play"><svg width="48" height="34" viewBox="0 0 48 34"><path d="M20 11l10 6-10 6z" fill="#fff"/></svg></div>
    <div class="video-track"></div>
    <div class="video-bar">00:03 / 10:03</div>
  </div>

  <h2 style="left:33px;top:244px">LATEST PHOTO ALBUM</h2>
  <p class="copy" style="left:33px;top:281px;width:362px">Past concert highlights include performances at Harbourside Hall, Saint Anselm Chapel in New York, and the Lakeland Music Educators Convention.</p>
  <div class="photo" style="left:53px;top:335px;background:linear-gradient(180deg,#cdb98f,#8a4a3a 60%,#7a2a2a)" role="img" aria-label="Choir in red jackets singing in a church"></div>
  <div class="photo" style="left:221px;top:335px;background:linear-gradient(180deg,#d8d8d6,#e8e8e6 55%,#6a6a6a)" role="img" aria-label="Choir in white robes before a pipe organ"></div>
  <div class="photo" style="left:53px;top:453px;background:linear-gradient(180deg,#2b2626,#4a3434 60%,#7a5a3a)" role="img" aria-label="Choir in striped blazers on stage"></div>
  <div class="photo" style="left:221px;top:453px;background:linear-gradient(180deg,#d9dcdc,#c6c9c8 50%,#a53a3a)" role="img" aria-label="Choir in red jackets standing in a courtyard"></div>
  <div class="view-all">View All Photos &gt;&gt;</div>

  <h2 style="left:424px;top:247px">LATEST NEWS &amp; EVENTS</h2>
  <div class="news">
    <div class="news-item" style="top:14px">
      <div class="news-thumb" style="background:linear-gradient(135deg,#6b4a36,#b9c2c8)" role="img" aria-label="Portrait of a member"></div>
      <div class="news-name">Tarmo Lill</div>
      <div class="news-handle">@choirdesk</div>
      <div class="news-date">22/11/2014 Monday</div>
      <div class="news-text">brightTrade Fast efficient polite service again today from your agents</div>
    </div>
    <div class="news-rule" style="top:100px"></div>
    <div class="news-item" style="top:109px">
      <div class="news-thumb" style="background:linear-gradient(180deg,#2a1a14,#d8b48e 45%,#8a1a1e)" role="img" aria-label="Portrait of a young singer in a red jacket"></div>
      <div class="news-name">Mari Kask</div>
      <div class="news-handle">@choirdesk</div>
      <div class="news-date">22/11/2014 Monday</div>
      <div class="news-text">brightTrade Fast efficient polite service again today from your agents</div>
    </div>
    <div class="news-rule" style="top:200px"></div>
    <div class="news-item" style="top:210px">
      <div class="news-thumb" style="background:linear-gradient(135deg,#d9e3ea,#c49a7a 50%,#6a4a32)" role="img" aria-label="Portrait of a member"></div>
      <div class="news-name">Priit Saar</div>
      <div class="news-handle">@choirdesk</div>
      <div class="news-date">22/11/2014 Monday</div>
      <div class="news-text">brightTrade Fast efficient polite service again today from your agents</div>
    </div>
  </div>
</main>

<footer class="site-footer">
  <div class="f-col" style="left:87px;top:17px"><h4>Quick links</h4>Our blog<br>Latest choirs<br>Downloads<br>Music</div>
  <div class="f-divider" style="left:191px"></div>
  <div class="f-col" style="left:221px;top:17px"><h4>Menu</h4>About us<br>Mission<br>Choir songs<br>Contact</div>
  <div class="f-divider" style="left:313px"></div>
  <div class="f-call">call us for enquiries<b>+65 6000 1834</b></div>
  <div class="f-mail">enquiries@kaskemaechoir.example</div>
  <div class="social" style="left:712px;background:#27a6df" aria-label="Social link"></div>
  <div class="social" style="left:742px;background:#3a5a9a" aria-label="Social link"></div>
  <div class="social" style="left:771px;background:#3ab0e8" aria-label="Social link"></div>
  <div class="f-line"></div>
  <div class="copyright">COPYRIGHT © 2014 KASKEMÄE MEESKOOR, ALL RIGHTS RESERVED</div>
</footer>

</body>
</html>
```